SOLVE Study flyer

I need help designing a flyer for a research study that will include brain imaging in adolescents. The info is in the attached document. The study is called the Sequoia Outlook Lantern Valley Echo (SOLVE) study. Ideally this would be returned as a document that I can edit in the future as we will have several new recruitment phases (different age groups, etc. I also would love to have a logo designed as part of this project, but I recognize that might be a separate design request.

```html
<!DOCTYPE html>
<html lang="en">
<head>
<meta charset="utf-8">
<title>SOLVE Study – Recruitment Flyer</title>
<link rel="stylesheet" href="https://fonts.googleapis.com/css2?family=Lexend:wght@400;600;700&family=Poppins:wght@300;400;500;600&display=swap">
<style>
  :root {
    --navy: #24215e;
    --purple: #5b3486;
    --circle-purple: #8c62b4;
    --lavender: #b597d6;
    --card-bg: #f1f0f8;
    --card-band: #e4e2f1;
    --divider: #cfcbe3;
    --gold: #fbb93a;
    --paper: #f2f2f2;
    --ink: #2e2c3d;
    --white: #ffffff;
  }
  * { box-sizing: border-box; margin: 0; padding: 0; }
  html, body { width: 927px; height: 1200px; overflow: hidden; background: var(--white); }
  body { font-family: "Poppins", sans-serif; color: var(--ink); }
  .flyer { position: relative; width: 927px; height: 1200px; overflow: hidden; background: var(--white); }

  /* Hero */
  .hero { position: absolute; left: 0; top: 0; width: 927px; height: 563px; background: var(--paper); overflow: hidden; }
  .hero-arc { position: absolute; left: 0; top: 0; }
  .hero-photo {
    position: absolute; left: 500px; top: 44px; width: 380px; height: 519px;
    border-radius: 190px 190px 0 0;
    background: linear-gradient(180deg, #c4a07f 0%, #b39075 30%, #a584c8 62%, #8f6cbd 100%);
  }

  .brand { position: absolute; left: 62px; top: 78px; display: flex; align-items: center; gap: 22px; color: var(--navy); }
  .brand-dot { width: 130px; height: 130px; border-radius: 50%; background: var(--navy); }
  .brand-text { display: flex; flex-direction: column; align-items: center; font-family: "Lexend", sans-serif; font-weight: 400; }
  .brand-name { font-size: 78px; line-height: 1; letter-spacing: 1px; }
  .brand-full { margin-top: 8px; font-size: 16px; line-height: 20px; letter-spacing: 1.2px; text-align: center; text-transform: uppercase; width: 250px; }

  .headline { position: absolute; left: 63px; top: 246px; width: 440px; font-family: "Lexend", sans-serif; font-weight: 700; font-size: 31px; line-height: 38px; }
  .headline-ask { color: var(--navy); }
  .headline-worry { color: var(--purple); }
  .headline-rule { position: absolute; left: 63px; top: 417px; width: 73px; height: 3px; background: var(--gold); }
  .intro { position: absolute; left: 63px; top: 439px; width: 440px; font-size: 15px; line-height: 23px; font-weight: 400; }
  .intro strong { color: var(--purple); font-weight: 600; }

  /* Cards */
  .card { position: absolute; top: 583px; width: 381px; height: 347px; background: var(--card-bg); border-radius: 22px; overflow: hidden; }
  .card-participation { left: 66px; }
  .card-eligibility { left: 480px; }
  .card-band { background: var(--card-band); padding-left: 72px; display: flex; align-items: center; font-family: "Poppins", sans-serif; font-weight: 600; color: var(--purple); text-transform: uppercase; }
  .card-participation .card-band { height: 38px; font-size: 15px; letter-spacing: 0.2px; padding-left: 72px; }
  .card-eligibility .card-band { height: 64px; font-size: 18px; line-height: 24px; padding-left: 68px; padding-top: 4px; }

  .card-badge { position: absolute; top: 568px; width: 66px; height: 66px; border-radius: 50%; display: flex; align-items: center; justify-content: center; }
  .badge-participation { left: 53px; background: var(--white); border: 2px solid var(--purple); }
  .badge-eligibility { left: 466px; background: var(--navy); border: 2px solid var(--lavender); }

  .step { position: absolute; left: 91px; width: 340px; display: flex; }
  .step-icon { width: 68px; height: 68px; border-radius: 50%; background: var(--circle-purple); display: flex; align-items: center; justify-content: center; flex-shrink: 0; }
  .step-text { position: absolute; left: 88px; width: 252px; font-size: 13.4px; line-height: 18px; color: var(--purple); }
  .step-title { font-family: "Poppins", sans-serif; font-weight: 600; font-size: 16px; line-height: 22px; color: var(--purple); }
  .step-rule { position: absolute; left: 180px; width: 241px; height: 1px; background: var(--divider); }

  .criterion { position: absolute; left: 518px; display: flex; }
  .criterion-tick { position: absolute; left: 0; }
  .criterion-text { position: absolute; left: 47px; width: 240px; font-size: 17px; line-height: 23px; color: var(--navy); }
  .criterion-text strong { color: var(--purple); font-weight: 600; }
  .criterion-age { font-family: "Lexend", sans-serif; font-weight: 600; font-size: 34px; line-height: 36px; color: var(--navy); }
  .criterion-rule { position: absolute; left: 556px; width: 240px; height: 1px; background: var(--divider); }

  /* Contact band */
  .contact-band { position: absolute; left: 0; top: 950px; width: 927px; height: 141px; background: var(--navy); }
  .band-circle { position: absolute; top: 29px; width: 84px; height: 84px; border-radius: 50%; background: var(--circle-purple); display: flex; align-items: center; justify-content: center; }
  .band-circle-mail { left: 64px; }
  .band-circle-gift { left: 529px; }
  .contact { position: absolute; left: 170px; top: 26px; width: 267px; text-align: center; color: var(--white); }
  .contact-title { font-weight: 600; font-size: 16px; line-height: 22px; color: var(--gold); text-transform: uppercase; }
  .contact-lead { font-size: 14px; line-height: 17px; margin-top: 4px; }
  .contact-email { margin-top: 8px; height: 27px; border-radius: 14px; background: var(--gold); color: var(--navy); font-weight: 600; font-size: 12.6px; line-height: 27px; }
  .band-divider { position: absolute; left: 463px; top: 20px; width: 1px; height: 101px; background: var(--white); opacity: 0.7; }
  .compensation { position: absolute; left: 646px; top: 38px; color: var(--white); }
  .compensation-title { font-weight: 600; font-size: 17px; line-height: 22px; color: var(--gold); text-transform: uppercase; }
  .compensation-upto { position: absolute; left: 0; top: 25px; font-size: 13px; }
  .compensation-amount { position: absolute; left: 54px; top: 10px; font-family: "Lexend", sans-serif; font-weight: 700; font-size: 64px; line-height: 1; color: var(--gold); letter-spacing: -1px; }

  /* Footer */
  .institution { position: absolute; left: 0; top: 1112px; width: 927px; display: flex; justify-content: center; align-items: center; gap: 12px; }
  .institution-mark { width: 44px; height: 44px; background: var(--navy); }
  .institution-name { font-family: "Lexend", sans-serif; font-weight: 600; font-size: 27px; color: var(--navy); }
</style>
</head>
<body>
<main class="flyer">

  <section class="hero">
    <svg class="hero-arc" width="927" height="563" viewBox="0 0 927 563" aria-hidden="true">
      <path d="M650,0 Q530,240 528,563 L927,563 L927,0 Z" fill="#b597d6"/>
      <path d="M662,0 Q542,240 540,563 L927,563 L927,0 Z" fill="#24215e"/>
    </svg>
    <div class="hero-photo" role="img" aria-label="Photo of a thoughtful young girl in a purple sweatshirt resting her chin on her hand, with a faint brain illustration behind her"></div>

    <div class="brand">
      <div class="brand-dot" aria-hidden="true"></div>
      <div class="brand-text">
        <span class="brand-name">SOLVE</span>
        <span class="brand-full">Sequoia Outlook Lantern Valley Echo Study</span>
      </div>
    </div>

    <h1 class="headline">
      <span class="headline-ask">Are you the parent of a child age 10-17?</span><br>
      <span class="headline-worry">Do they worry or overthink negative emotions?</span>
    </h1>
    <div class="headline-rule"></div>
    <p class="intro">Northfield University researchers are seeking <strong>girls age 10-17</strong> for a study about brain activity in emotions and decision-making and how they relate to puberty, anxiety and depression.</p>
  </section>

  <!-- Participation card -->
  <section class="card card-participation">
    <h2 class="card-band">Study participation involves:</h2>
  </section>
  <div class="card-badge badge-participation" aria-hidden="true">
    <svg width="40" height="40" viewBox="0 0 40 40" fill="none" stroke="#5b3486" stroke-width="2.2" stroke-linecap="round" stroke-linejoin="round">
      <circle cx="20" cy="9" r="5" fill="#5b3486"/>
      <path d="M11 24 Q20 14 29 24"/>
      <path d="M5 25 L20 29 L35 25 M5 30 L20 34 L35 30 M20 29 V34"/>
    </svg>
  </div>

  <div class="step" style="top:642px">
    <div class="step-icon" aria-hidden="true">
      <svg width="36" height="36" viewBox="0 0 36 36" fill="none" stroke="#fff" stroke-width="2" stroke-linecap="round" stroke-linejoin="round">
        <path d="M4 6 H26 V22 H12 L6 27 V22 H4 Z"/>
        <path d="M8 11 H20 M8 15 H18"/>
        <rect x="25" y="16" width="5" height="9" rx="2.5"/>
        <path d="M23 22 Q27.5 29 32 22 M27.5 27 V31"/>
      </svg>
    </div>
    <div class="step-text" style="top:2px">
      <div class="step-title">One one-hour interview</div>
      (online or in-person) where your child will discuss their thoughts
    </div>
  </div>
  <div class="step-rule" style="top:723px"></div>

  <div class="step" style="top:728px">
    <div class="step-icon" aria-hidden="true">
      <svg width="34" height="34" viewBox="0 0 34 34" fill="none" stroke="#fff" stroke-width="2" stroke-linecap="round" stroke-linejoin="round">
        <path d="M9 3 H21 L26 8 V31 H9 Z"/>
        <rect x="12" y="9" width="4" height="4"/>
        <rect x="12" y="16" width="4" height="4"/>
        <rect x="12" y="23" width="4" height="4"/>
        <path d="M12.5 25 L14 26.5 L17 22.5"/>
        <circle cx="22" cy="27" r="0.6"/>
      </svg>
    </div>
    <div class="step-text" style="top:11px">
      <div class="step-title">Online questionnaires</div>
      (parent and child)
    </div>
  </div>
  <div class="step-rule" style="top:798px"></div>

  <div class="step" style="top:829px">
    <div class="step-icon" aria-hidden="true">
      <svg width="36" height="36" viewBox="0 0 36 36" fill="none" stroke="#fff" stroke-width="2" stroke-linecap="round" stroke-linejoin="round">
        <circle cx="18" cy="15" r="10"/>
        <circle cx="18" cy="15" r="5"/>
        <path d="M5 31 H31 M8 31 V24 M28 31 V24 M10 24 H26"/>
      </svg>
    </div>
    <div class="step-text" style="top:-23px">
      <div class="step-title">One two-hour visit</div>
      where your child will complete an MRI scan, answer questions about their puberty stage, and have a small hair sample taken to study puberty hormones
    </div>
  </div>

  <!-- Eligibility card -->
  <section class="card card-eligibility">
    <h2 class="card-band">Your child may be eligible if they:</h2>
  </section>
  <div class="card-badge badge-eligibility" aria-hidden="true">
    <svg width="40" height="40" viewBox="0 0 40 40">
      <circle cx="20" cy="20" r="18" fill="#fff"/>
      <path d="M20 9 L23.2 16 L30.5 16.6 L25 21.6 L26.7 29 L20 25 L13.3 29 L15 21.6 L9.5 16.6 L16.8 16 Z" fill="#24215e" stroke="#24215e" stroke-width="2" stroke-linejoin="round"/>
    </svg>
  </div>

  <div class="criterion" style="top:672px">
    <svg class="criterion-tick" width="28" height="28" viewBox="0 0 28 28" fill="none" stroke="#fbb93a" stroke-width="2.4" stroke-linecap="round" stroke-linejoin="round" aria-hidden="true">
      <path d="M25 12 A12 12 0 1 1 19 3.5"/><path d="M8 13 L13 18 L25 5"/>
    </svg>
    <div class="criterion-text" style="top:-4px">Are age<div class="criterion-age">10-17</div></div>
  </div>
  <div class="criterion-rule" style="top:734px"></div>

  <div class="criterion" style="top:761px">
    <svg class="criterion-tick" width="28" height="28" viewBox="0 0 28 28" fill="none" stroke="#fbb93a" stroke-width="2.4" stroke-linecap="round" stroke-linejoin="round" aria-hidden="true">
      <path d="M25 12 A12 12 0 1 1 19 3.5"/><path d="M8 13 L13 18 L25 5"/>
    </svg>
    <div class="criterion-text" style="top:-11px; left:47px">Tend to <strong>worry or overthink</strong> negative thoughts</div>
  </div>
  <div class="criterion-rule" style="top:813px"></div>

  <div class="criterion" style="top:836px">
    <svg class="criterion-tick" width="28" height="28" viewBox="0 0 28 28" fill="none" stroke="#fbb93a" stroke-width="2.4" stroke-linecap="round" stroke-linejoin="round" aria-hidden="true">
      <path d="M25 12 A12 12 0 1 1 19 3.5"/><path d="M8 13 L13 18 L25 5"/>
    </svg>
    <div class="criterion-text" style="top:-5px">Have not been diagnosed with psychosis, learning problems, or autism</div>
  </div>

  <!-- Contact + compensation -->
  <section class="contact-band">
    <div class="band-circle band-circle-mail" aria-hidden="true">
      <svg width="50" height="36" viewBox="0 0 50 36" fill="none" stroke="#fff" stroke-width="2.6" stroke-linejoin="round">
        <rect x="2" y="2" width="46" height="32" rx="3"/>
        <path d="M2 4 L25 21 L48 4 M2 33 L19 17 M48 33 L31 17"/>
      </svg>
    </div>
    <div class="contact">
      <div class="contact-title">Interested in participating?</div>
      <div class="contact-lead">Want more information?<br>Please contact us!</div>
      <div class="contact-email">solvestudy@northfield-health.edu</div>
    </div>
    <div class="band-divider"></div>
    <div class="band-circle band-circle-gift" aria-hidden="true">
      <svg width="44" height="38" viewBox="0 0 44 38" fill="none" stroke="#fff" stroke-width="2.4" stroke-linejoin="round">
        <rect x="2" y="2" width="40" height="34" rx="2"/>
        <path d="M2 14 H42 M16 2 V36"/>
        <path d="M16 14 Q10 6 12 5 Q15 4 16 14 Q17 4 20 5 Q22 6 16 14 L11 21 M16 14 L21 21"/>
      </svg>
    </div>
    <div class="compensation">
      <div class="compensation-title">Compensation</div>
      <div class="compensation-upto">UP TO</div>
      <div class="compensation-amount">$140</div>
    </div>
  </section>

  <footer class="institution">
    <div class="institution-mark" aria-hidden="true"></div>
    <div class="institution-name">Northfield University</div>
  </footer>

</main>
</body>
</html>
```